Redesign of business card for Cedar Ridge Mechanical

We are looking for a new design for our business cards for Cedar Ridge Mechanical. We are a plumbing & HVAC construction company, operating on the West Coast of Canada and USA. Logo attached.
Industry/Entity Type
Construction - Plumbing & HVAC
Contact Information for Business Card
Name, address, phone numbers, email, website address
Look and feel
Each slider illustrates characteristics of the customer's brand and the style your logo design should communicate.

```html
<!DOCTYPE html>
<html lang="en">
<head>
<meta charset="utf-8">
<title>Cedar Ridge Mechanical – Business Card</title>
<link rel="stylesheet" href="https://fonts.googleapis.com/css2?family=Arimo:wght@400;700&display=swap">
<style>
  :root {
    --page-bg: #d9d9d9;
    --card-dark: #323232;
    --card-light: #ffffff;
    --ink-light: #ffffff;
    --ink-muted: #e4e4e4;
    --ink-dark: #111111;
    --divider: #8a8a8a;
  }
  * { margin: 0; padding: 0; box-sizing: border-box; }
  html, body {
    width: 1200px;
    height: 800px;
    overflow: hidden;
    background: var(--page-bg);
    font-family: "Arimo", Arial, sans-serif;
  }
  .canvas {
    width: 1200px;
    height: 800px;
    display: flex;
    align-items: center;
    justify-content: center;
    gap: 40px;
  }
  .card {
    width: 520px;
    height: 297px;
    border-radius: 22px;
    box-shadow: 0 10px 24px rgba(0,0,0,0.18);
    position: relative;
  }
  .card-back {
    background: var(--card-dark);
    color: var(--ink-light);
    display: flex;
    align-items: center;
    padding: 0 40px 0 44px;
  }
  .identity {
    width: 150px;
    text-align: right;
    padding-right: 22px;
  }
  .identity .person-name {
    font-weight: 700;
    font-size: 21px;
    letter-spacing: 0.2px;
  }
  .identity .person-title {
    font-size: 15px;
    color: var(--ink-muted);
    margin-top: 4px;
  }
  .divider {
    width: 1px;
    height: 118px;
    background: var(--divider);
  }
  .contact {
    padding-left: 22px;
    font-size: 14px;
    line-height: 1.45;
    color: var(--ink-muted);
  }
  .contact .address { margin-bottom: 10px; }
  .contact .label {
    font-weight: 700;
    color: var(--ink-light);
    display: inline-block;
    width: 26px;
  }
  .card-front {
    background: var(--card-light);
    display: flex;
    align-items: center;
    justify-content: center;
  }
  .brand {
    display: flex;
    align-items: center;
    gap: 14px;
  }
  .brand-square {
    width: 34px;
    height: 34px;
    background: var(--ink-dark);
  }
  .brand-name {
    font-weight: 700;
    font-size: 24px;
    letter-spacing: 1.5px;
    text-transform: uppercase;
    color: var(--ink-dark);
  }
</style>
</head>
<body>
  <main class="canvas">
    <section class="card card-back" aria-label="Card back with contact details">
      <div class="identity">
        <p class="person-name">Daniel Harper</p>
        <p class="person-title">President</p>
      </div>
      <div class="divider"></div>
      <div class="contact">
        <p class="address">4170 Larchmont Avenue<br>Brookfield, NY 11204</p>
        <p><span class="label">P :</span>(604) 5821-3390</p>
        <p><span class="label">E :</span>name@cedarridgemechanical.com</p>
        <p><span class="label">W :</span>www.cedarridgemechanical.com</p>
      </div>
    </section>
    <section class="card card-front" aria-label="Card front with company name">
      <div class="brand">
        <span class="brand-square"></span>
        <span class="brand-name">Cedar Ridge Mechanical</span>
      </div>
    </section>
  </main>
</body>
</html>
```